Card design for orthopaedic surgeons working as The Brightwater Joint Centre

Business cards, letterhead

Colors

Designer to choose colors to be used in the design.

Requirements
Must have
• Late addition.
• Cards letterhead must have logos of
• Crestmoor Lindell College of Surgeons
• Varenwood Bone Health Association
Nice to have
• Back of card to have space for appointment time to be added by hand and some blank space for writing incidental other notes.

```html
<!DOCTYPE html>
<html lang="en">
<head>
<meta charset="utf-8">
<title>The Brightwater Joint Centre – Business Card</title>
<link rel="stylesheet" href="https://fonts.googleapis.com/css2?family=Roboto:wght@400;500&display=swap">
<style>
  :root {
    --page-bg: #d6d6d6;
    --card-white: #ffffff;
    --brand-blue: #58ade0;
    --accent-blue: #4aa8e0;
    --ink: #2b3a4a;
    --navy: #1f3a56;
    --shadow: rgba(0, 0, 0, 0.35);
  }
  * { box-sizing: border-box; margin: 0; padding: 0; }
  html, body {
    width: 1125px; height: 1200px; overflow: hidden;
    background: var(--page-bg);
    font-family: "Roboto", Arial, sans-serif;
    color: var(--ink);
  }
  .card {
    position: absolute; left: 150px; width: 825px; height: 472px;
    border-radius: 24px;
    box-shadow: 2px 4px 6px var(--shadow);
  }
  .card-front { top: 98px; background: var(--card-white); }
  .card-back { top: 631px; background: var(--brand-blue); }

  .brand-name {
    position: absolute; font-weight: 400; white-space: nowrap;
    display: flex; align-items: center; gap: 10px;
  }
  .brand-name .dot { border-radius: 50%; display: inline-block; }
  .card-front .brand-name {
    left: 66px; top: 222px; font-size: 25px; color: var(--accent-blue);
  }
  .card-front .brand-name .dot { width: 14px; height: 14px; background: var(--accent-blue); }
  .card-back .brand-name {
    left: 0; right: 0; justify-content: center; top: 212px;
    font-size: 40px; color: var(--card-white);
  }
  .card-back .brand-name .dot { width: 20px; height: 20px; background: var(--card-white); }

  .divider {
    position: absolute; left: 411px; top: 165px; width: 2px; height: 140px;
    background: var(--navy);
  }
  .contact-block { position: absolute; left: 453px; top: 158px; }
  .person-name { font-size: 32px; font-weight: 500; color: var(--accent-blue); line-height: 1.1; }
  .person-role { font-size: 18px; color: var(--ink); margin-top: 2px; }
  .contact-list { list-style: none; margin-top: 22px; }
  .contact-list li {
    display: flex; align-items: center; gap: 8px;
    font-size: 19px; line-height: 24px; color: var(--ink);
  }
  .contact-list svg { width: 14px; height: 14px; flex: none; }
  .contact-list .highlight { color: var(--accent-blue); }
  .address {
    position: absolute; left: 0; right: 0; top: 418px;
    text-align: center; font-size: 19px; color: var(--ink);
  }
</style>
</head>
<body>
  <section class="card card-front">
    <div class="brand-name"><span class="dot"></span>The Brightwater Joint Centre</div>
    <div class="divider"></div>
    <div class="contact-block">
      <h1 class="person-name">John Smith</h1>
      <p class="person-role">Manager</p>
      <ul class="contact-list">
        <li>
          <svg viewBox="0 0 16 16"><path fill="#4aa8e0" d="M3.5 1.5l2.5 0 1.2 3.2-1.6 1.3c.9 1.9 2.3 3.3 4.2 4.2l1.3-1.6 3.2 1.2v2.5c0 .9-.8 1.6-1.7 1.5C6.9 13.3 2.7 9.1 2 3.2 1.9 2.3 2.6 1.5 3.5 1.5z"/></svg>
          123-456-2100
        </li>
        <li>
          <svg viewBox="0 0 16 16"><rect x="1" y="3.5" width="14" height="9" fill="#4aa8e0"/><path d="M1 3.5l7 5 7-5" fill="none" stroke="#fff" stroke-width="1.3"/></svg>
          youremail@brightwatermail.com
        </li>
        <li>
          <svg viewBox="0 0 16 16"><circle cx="8" cy="8" r="7" fill="#4aa8e0"/><path d="M1 8h14M8 1c-2.5 2-2.5 12 0 14M8 1c2.5 2 2.5 12 0 14" fill="none" stroke="#fff" stroke-width="1"/></svg>
          <span>www.<span class="highlight">yourwebsite</span>.com</span>
        </li>
      </ul>
    </div>
    <p class="address">Your address, city, state, ZIP 0000</p>
  </section>

  <section class="card card-back">
    <div class="brand-name"><span class="dot"></span>The Brightwater Joint Centre</div>
  </section>
</body>
</html>
```